website design Investment Fund

I am looking for a custom website that will work on desktop computer, tablet device and a cellular device. I have attached the booklet so you can get an idea of the look we are going for. Would like to use the website eventually for crowdfunding. We like the ski racer and mountain climbing designs.

Target Market(s)

Financial Services

Industry/Entity Type

Financial Service

Coding

Coded - Design and coding required

Number of Pages Required

5+ page

Font styles to use
Sans Serif

Requirements
Must have
• Must be viewable on a cell phone and tablet and desktop
Nice to have
• Contact us form

```html
<!DOCTYPE html>
<html lang="en">
<head>
<meta charset="utf-8">
<title>Vantor Capital II — Secured Income Fund</title>
<link href="https://fonts.googleapis.com/css2?family=Montserrat:wght@600;700;800&family=Mulish:wght@400;600;700&display=swap" rel="stylesheet">
<style>
:root{
  --red:#e30613;
  --blue:#1d47a1;
  --blue-deep:#173b8c;
  --navy:#1a3a8f;
  --ink:#444;
  --white:#fff;
  --black:#0c0c0c;
  --snow:#eef1f5;
}
*{margin:0;padding:0;box-sizing:border-box}
html,body{width:1200px;height:5013px;overflow:hidden}
body{position:relative;font-family:'Mulish',sans-serif;color:var(--ink);background:var(--white)}
.abs{position:absolute}
.head{font-family:'Montserrat',sans-serif;font-weight:800;text-transform:uppercase}
.center{text-align:center;left:0;width:1200px}
.btn{position:absolute;background:var(--red);color:var(--white);font-family:'Montserrat',sans-serif;font-weight:700;font-size:15px;text-transform:uppercase;border-radius:26px;display:flex;align-items:center;justify-content:center}

/* hero */
.hero-photo{left:0;top:0;width:1200px;height:1120px;background:linear-gradient(180deg,#5a7fb8 0%,#8fa9cf 30%,#c8d5e6 55%,#eef2f7 80%,#fff 100%)}
.brand{left:171px;top:76px;color:var(--white);font-family:'Montserrat',sans-serif;font-weight:800;font-size:24px;line-height:1}
.brand small{display:block;font-size:14px;font-weight:800;margin-top:4px;padding-left:14px}
.brand-dot{left:286px;top:14px;width:46px;height:46px;background:var(--white);border-radius:50%}
.nav{top:86px;left:500px;display:flex;gap:37px;color:var(--white);font-family:'Montserrat',sans-serif;font-weight:700;font-size:13px}
.quote{left:880px;top:23px;width:147px;height:38px;border-radius:3px;font-size:14px}
.hero-title{left:170px;top:290px;color:var(--white);font-size:56px;letter-spacing:1px}
.hero-sub{left:173px;top:358px;color:var(--navy);font-size:28px}
.read{left:173px;top:424px;width:145px;height:44px}

/* welcome */
.eyebrow{font-family:'Montserrat',sans-serif;font-weight:700;color:var(--red);font-size:24px;text-transform:uppercase}
.title-blue{color:var(--navy);font-size:50px}
.copy{font-size:11.5px;line-height:25px;text-align:center}
.welcome-bg{left:0;top:1400px;width:1200px;height:280px;background:linear-gradient(180deg,#fff,#d9dee6)}
.skier-two{left:914px;top:1255px;width:286px;height:422px;background:linear-gradient(160deg,#2b4e9e,#c9d2e0 60%,#e9edf3);border-radius:4px}

/* fund band */
.fund{left:0;top:1677px;width:1200px;height:680px;background:var(--blue)}
.fund .copy{color:var(--white)}
.white-head{color:var(--white);font-family:'Montserrat',sans-serif;font-weight:700;text-transform:uppercase}

/* accredited */
.peak{width:409px;height:228px;top:2460px}
.tier-h{font-family:'Montserrat',sans-serif;font-weight:700;font-size:17px;color:#222;top:2715px}
.tier-s{font-family:'Montserrat',sans-serif;font-weight:700;font-size:20px;color:var(--red);top:2750px}
.tier-p{font-size:10.5px;line-height:24px;top:2800px;width:409px}

/* team */
.team-bg{left:0;top:2950px;width:1200px;height:700px;background:linear-gradient(180deg,#eef1f5,#fff 30%,#e6eaf0 100%)}
.avatar{width:155px;height:155px;border-radius:50%;border:4px solid var(--red);background:linear-gradient(160deg,#c9ccd2,#8d939c)}
.flag{width:22px;height:22px;background:var(--blue);border-radius:50%}
.first{font-family:'Montserrat',sans-serif;font-weight:700;color:var(--red);font-size:16px;text-transform:uppercase}
.last{color:var(--navy);font-size:24px;text-transform:uppercase;font-weight:400}
.bio{font-size:10.5px;line-height:22px;width:220px}

/* contact */
.contact{left:0;top:4020px;width:1200px;height:680px;background:linear-gradient(180deg,var(--blue) 0%,var(--blue-deep) 100%)}
.field{background:var(--white);border-radius:3px;font-size:12px;color:#555;padding:12px 16px}
.submit{left:512px;top:4376px;width:175px;height:51px}
.sign-mark{left:175px;top:4530px;width:110px;height:110px;background:var(--white)}
.sign{left:315px;top:4510px;color:var(--white)}
.sign-name{font-family:'Montserrat',sans-serif;font-weight:800;font-size:44px}
.sign-sub{font-family:'Montserrat',sans-serif;font-weight:600;font-size:28px;margin-top:-4px}
.sign-addr{font-size:22px;border-top:2px solid var(--white);margin-top:6px;padding-top:6px;width:655px}

/* footer */
.footer{left:0;top:4697px;width:1200px;height:316px;background:var(--black);color:var(--white)}
.foot-brand{top:115px;font-family:'Montserrat',sans-serif;font-weight:800;font-size:20px}
.foot-dot{left:575px;top:28px;width:50px;height:50px;border-radius:50%;background:var(--blue)}
.foot-nav{top:178px;display:flex;justify-content:center;gap:22px;font-size:12px;font-weight:600}
.social{top:222px;display:flex;justify-content:center;gap:8px}
.social span{width:30px;height:30px;border:2px solid var(--white);border-radius:50%}
.copyright{top:276px;font-size:11px}
</style>
</head>
<body>

<!-- hero -->
<div class="abs hero-photo" role="img" aria-label="Downhill skier carving through snow beneath snowy mountain peaks"></div>
<svg class="abs" style="left:0;top:640px" width="1200" height="480" viewBox="0 0 1200 480">
  <polygon points="0,12 430,445 0,190" fill="#e30613"/>
  <polygon points="1200,12 430,445 1200,170" fill="#e30613"/>
  <polygon points="0,186 290,362 0,480" fill="#1d47a1"/>
  <polygon points="1200,170 720,400 1200,443" fill="#1d47a1"/>
  <polygon points="0,480 290,362 430,445 720,400 1200,443 1200,480" fill="#fff"/>
</svg>
<div class="abs brand-dot"></div>
<div class="abs brand">VANTOR CAPITAL II<small>SECURED INCOME FUND</small></div>
<div class="btn quote">Get a quote</div>
<nav class="abs nav"><span>HOME</span><span>ABOUT US</span><span>SERVICES</span><span>TEAM</span><span>NEWS</span><span>CONTACT US</span></nav>
<h1 class="abs head hero-title">Vantor Capital II</h1>
<h2 class="abs head hero-sub">Arizona’s Elite Boutique Lender</h2>
<div class="btn read">Read more</div>

<!-- welcome -->
<div class="abs welcome-bg" role="img" aria-label="Misty mountain range fading into white"></div>
<div class="abs skier-two" role="img" aria-label="Slalom racer leaning past a gate"></div>
<p class="abs center eyebrow" style="top:1120px">Welcome to</p>
<h2 class="abs center head title-blue" style="top:1150px">Vantor Capital II</h2>
<p class="abs copy" style="left:306px;top:1232px;width:594px">Valmont Funding &amp; Investment, Inc. is a privately held mortgage lender, asset management and advisory firm headquartered in Scottsdale, Arizona which specializes in fast financing for debt, equity, mezzanine and land bank on real estate projects in the $100,000 to $50,000,000 rang . As a highly reputable, successful and growth-focused company with decades of experience across the entire spectrum of real estate financing through Arizona, the Southwest United States and Mexico We’re proud of the incomparable personal service and years of combined experience we bring to each and every to mitigate risk and bring our clients and partners a fast and efficient closing process.</p>
<div class="btn" style="left:484px;top:1420px;width:232px;height:50px;font-size:13px">Click here for more info</div>

<!-- fund -->
<div class="abs fund" role="img" aria-label="Blue-tinted ski racing course with banners"></div>
<svg class="abs" style="left:0;top:1677px" width="1200" height="680" viewBox="0 0 1200 680">
  <polygon points="0,0 240,0 0,250" fill="#e30613"/>
  <polygon points="1200,360 1200,534 880,534" fill="#e30613"/>
  <polygon points="0,680 1200,534 1200,680" fill="#fff"/>
</svg>
<p class="abs center white-head" style="top:1738px;font-size:28px">The Boutique Fund</p>
<p class="abs center white-head" style="top:1782px;font-size:40px">Investors are looking for</p>
<p class="abs copy" style="left:285px;top:1852px;width:630px;font-size:11.5px">Lead by its Founder and Chairman who is a seasoned Mortgage/Finance and real estate development specialist with 37 years of Entrepreneurial experience and 23 years in the Private Lender business, Valmont has funded and facilitated over $1 Billion in private money, equity, Institutional and Mezzanine loans and growing We’re proud of the incomparable personal service and years of combined experience we which enables us to mitigate risk and bring our clients and partners a fast and efficient closing process.</p>
<p class="abs center white-head" style="top:1992px;font-size:40px">Investment Strategy</p>
<p class="abs copy" style="left:285px;top:2060px;width:630px">At Valmont, we’ve created an exceptional business focused on delivering privately funded financing to a wide range of clients. Our proven diligence, impeccable operating standards and expertise help to ensure that the funding process will run more rapidly and reliably than any other companyin that market.</p>

<!-- accredited -->
<p class="abs center eyebrow" style="top:2324px">Accredited</p>
<h2 class="abs center head title-blue" style="top:2352px;font-size:52px">Investors only</h2>
<div class="abs peak" style="left:173px;background:linear-gradient(180deg,#3c4e5c,#6d7d88 55%,#232a30)" role="img" aria-label="Climber standing before a moonlit mountain"></div>
<div class="abs peak" style="left:617px;background:linear-gradient(180deg,#56646e,#a4adb4 50%,#2a3136)" role="img" aria-label="Sharp rocky summit under cloudy sky"></div>
<p class="abs tier-h" style="left:173px">Minimum Investment Requirements</p>
<p class="abs tier-s" style="left:173px">SERIES A $50,000-$249,999</p>
<p class="abs tier-p" style="left:173px">At Valmont, we’ve created an exceptional business focused on delivering privately funded financing to a wide range of clients. Our proven diligence, impeccable operating standards and expertise help to ensure that the funding process will run more rapidly and reliably than any other company in that market.</p>
<p class="abs tier-h" style="left:617px">Minimum Investment Requirements</p>
<p class="abs tier-s" style="left:617px">SERIES B $250,000.00</p>
<p class="abs tier-p" style="left:617px">At Valmont, we’ve created an exceptional business focused on delivering privately funded financing to a wide range of clients. Our proven diligence, impeccable operating standards and expertise help to ensure that the funding process will run more rapidly and reliably than any other company in that market.</p>

<!-- team -->
<div class="abs team-bg" role="img" aria-label="Pale misty mountain backdrop"></div>
<p class="abs center eyebrow" style="top:3016px">Vantor Capital II</p>
<h2 class="abs center head title-blue" style="top:3044px">Our Team</h2>

<div class="abs avatar" style="left:173px;top:3135px" role="img" aria-label="Portrait of team member"></div>
<div class="abs flag" style="left:305px;top:3128px"></div>
<p class="abs first" style="left:358px;top:3145px">Mark D</p>
<p class="abs last" style="left:358px;top:3166px">Hallbrook</p>
<p class="abs bio" style="left:358px;top:3205px">Mark is a real estate development &amp; finance entrepreneur &amp; executive with over 37 years of entrepreneur experience. As the Founder, Chairman and CEO of Valmont Funding and Investments, Inc, a privately</p>

<div class="abs avatar" style="left:628px;top:3135px" role="img" aria-label="Portrait of team member"></div>
<div class="abs flag" style="left:760px;top:3128px"></div>
<p class="abs first" style="left:813px;top:3145px">Dawn</p>
<p class="abs last" style="left:813px;top:3166px">Westlake</p>
<p class="abs bio" style="left:813px;top:3205px">for helping to educate Investors on alternative investment strategies by to earn a higher rate of return. In this Capital II Management’s relationship with the community and overseesstrategic investments through the with prop improvements</p>

<div class="abs avatar" style="left:173px;top:3400px" role="img" aria-label="Portrait of team member"></div>
<div class="abs flag" style="left:305px;top:3393px"></div>
<p class="abs first" style="left:358px;top:3410px">Tom</p>
<p class="abs last" style="left:358px;top:3431px">Brennick</p>
<p class="abs bio" style="left:358px;top:3470px">Tom brings over 20 years of wide-ranging experience in financial services with a focus on building industry leading franchises at global investment banks including Harlow Brothers and Kellerstadt Bank.</p>

<div class="abs avatar" style="left:628px;top:3400px" role="img" aria-label="Portrait of team member"></div>
<div class="abs flag" style="left:760px;top:3393px"></div>
<p class="abs first" style="left:813px;top:3410px">Joe</p>
<p class="abs last" style="left:813px;top:3431px">Alden</p>
<p class="abs bio" style="left:813px;top:3470px">With over 35 years of experience as a financial &amp; operational executive industry experience has principally been in the real estate lending and real estate development experi including but not limited</p>

<svg class="abs" style="left:0;top:3480px" width="1200" height="560" viewBox="0 0 1200 560">
  <polygon points="0,300 400,400 1200,180 1200,560 0,560" fill="#1d47a1"/>
  <polygon points="1200,20 400,400 1200,180" fill="#e30613"/>
  <polygon points="0,220 290,370 0,540" fill="#e30613"/>
</svg>

<!-- contact -->
<div class="abs contact" role="img" aria-label="Blue-tinted climbers on a mountain ridge"></div>
<p class="abs center eyebrow" style="top:4022px;color:#c0283a">Vantor Capital II</p>
<h2 class="abs center head" style="top:4054px;color:var(--white);font-size:50px">Contact us</h2>
<div class="abs field" style="left:321px;top:4157px;width:272px;height:40px">First Name :</div>
<div class="abs field" style="left:609px;top:4157px;width:270px;height:40px">Last Name :</div>
<div class="abs field" style="left:321px;top:4211px;width:272px;height:41px">Email :</div>
<div class="abs field" style="left:609px;top:4211px;width:270px;height:41px">Phone :</div>
<div class="abs field" style="left:321px;top:4265px;width:558px;height:86px">Message :</div>
<div class="btn submit">Submit</div>
<div class="abs sign-mark"></div>
<div class="abs sign">
  <div class="sign-name">VANTOR CAPITAL II</div>
  <div class="sign-sub">MANAGEMENT, LLC</div>
  <div class="sign-addr">2200 N. Canyon Ridge Blvd Suite 14 Scottsdale, AZ 85260</div>
</div>

<!-- footer -->
<footer class="abs footer">
  <div class="abs foot-dot"></div>
  <p class="abs center foot-brand">VANTOR CAPITAL II</p>
  <nav class="abs center foot-nav"><span>HOME</span><span>/</span><span>ABOUT US</span><span>/</span><span>SERVICES</span><span>/</span><span>TEAM</span><span>/</span><span>NEWS</span><span>/</span><span>CONTACT US</span></nav>
  <div class="abs center social"><span></span><span></span><span></span><span></span><span></span></div>
  <p class="abs center copyright">Copyrights © 2019 Vantor Capital II All Rights Reserved</p>
</footer>

</body>
</html>
```